Bram Keystone Homes needs a business card

We need a business card for a new company in Canada, Ontario. Our company is all about luxury contraction homes for our clients. Our product and services are custom projects design. Under the business logo that will be created, we want a slogan that will be a memorable phrase for consumers to remember us to tell their friends and relatives.

Additional infomation
- Ludovic Entrasse
- President / Ceo
-519.604.3087

Find point what luxury construction products and services can be done

We like to see colors:
- #663300
- and something other colors or color that would attract the client needs and wants

The final design should communicate leads from new or old clients that will grow our empire. Most of all, we try to work among the budget that clients want

NOTE
- we also need an icon for the business (Example: Instagram, Facebook, and Whatsapp icons)
- We want the company name to be remembered easily for clients and our distributors who would get our orders.
- we need an icon on the business cards: Facebook and Instagram.

Thanks,
Bram Keystone Homes

```html
<!DOCTYPE html>
<html lang="en">
<head>
<meta charset="utf-8">
<title>Bram Keystone Homes – Business Card</title>
<link rel="stylesheet" href="https://fonts.googleapis.com/css2?family=Poppins:wght@400;500;700&family=Roboto+Condensed:wght@500&display=swap">
<style>
  :root {
    --backdrop: #e4e4e4;
    --card-top: #2a2b2d;
    --card-bottom: #1b1c1e;
    --bronze: #7a3f02;
    --bronze-line: #663300;
  }
  * { margin: 0; padding: 0; box-sizing: border-box; }
  html, body {
    width: 1200px;
    height: 1200px;
    overflow: hidden;
    background: var(--backdrop);
  }
  .sheet {
    position: relative;
    width: 1200px;
    height: 1200px;
  }
  .card {
    position: absolute;
    left: 257px;
    width: 686px;
    height: 392px;
    background: linear-gradient(180deg, var(--card-top) 0%, var(--card-bottom) 100%);
    color: var(--bronze);
    font-family: "Poppins", sans-serif;
  }
  .card--front { top: 165px; }
  .card--back { top: 653px; }
  .card__frame {
    position: absolute;
    inset: 15px 16px 15px 16px;
    border: 1.5px solid var(--bronze-line);
  }
  .contact {
    position: absolute;
    left: 0;
    right: 0;
    top: 144px;
    text-align: center;
  }
  .contact__phone {
    font-weight: 500;
    font-size: 22px;
    letter-spacing: 0.3px;
    line-height: 30px;
  }
  .contact__name {
    margin-top: 2px;
    font-weight: 500;
    font-size: 21px;
    line-height: 30px;
    padding-left: 40px;
  }
  .contact__role {
    font-size: 17px;
    font-weight: 500;
  }
  .social {
    display: flex;
    justify-content: center;
    align-items: center;
    gap: 3px;
    margin-top: 6px;
  }
  .social__rule {
    width: 32px;
    height: 1.5px;
    background: var(--bronze);
    margin: 0 5px;
  }
  .social__icon {
    width: 29px;
    height: 29px;
    border: 1.5px solid var(--bronze);
    border-radius: 50%;
  }
  .brand {
    position: absolute;
    left: 0;
    right: 0;
    top: 155px;
    text-align: center;
  }
  .brand__name {
    font-weight: 700;
    font-size: 38px;
    line-height: 48px;
    letter-spacing: -0.5px;
  }
  .brand__tagline {
    font-family: "Roboto Condensed", sans-serif;
    font-weight: 500;
    font-size: 18px;
    line-height: 22px;
    margin-top: 2px;
  }
</style>
</head>
<body>
<main class="sheet">
  <section class="card card--front">
    <div class="card__frame"></div>
    <div class="contact">
      <p class="contact__phone">519.604.3087</p>
      <p class="contact__name">Ludovic Entrasse <span class="contact__role">– President / Ceo</span></p>
      <div class="social" role="img" aria-label="Social media icons">
        <span class="social__rule"></span>
        <span class="social__icon"></span>
        <span class="social__icon"></span>
        <span class="social__icon"></span>
        <span class="social__rule"></span>
      </div>
    </div>
  </section>

  <section class="card card--back">
    <div class="card__frame"></div>
    <div class="brand">
      <p class="brand__name">Bram Keystone Homes</p>
      <p class="brand__tagline">- HOME RENOVATIONS - CUSTOM PROJECT DESIGN -</p>
    </div>
  </section>
</main>
</body>
</html>
```